Business Card Design For Marketing Agnecy LVP

Need business card design for marketing agency.

Doug Fenwick
President, CEO
1-555-302-4196
doug@boldpromoperksgroup.example
www.BoldPromoPerksGroup.example

Back Side:
Boost Sales Using Rewards, Incentives & Giveaways
Get A Free Sample Package

Target Market(s)

B2B

Industry/Entity Type

Marketing

Contact Information for Business Card

Doug Fenwick
President, CEO
1-555-302-4196

Back Side:
Get A Free Sample Package

Please note that my current url is OLD DESIGN. I am working on new design and want the business card to match color themes at least on new site. Here is the demo link for new site so you can see the colors I use, etc.

http://layoutcratehub.example/kq/doug/lvp_final/index.html

Requirements
Must have
• Please note that my current url is OLD DESIGN. I am working on new design and want the business card to match color themes at least on new site. Here is the demo link for new site so you can see the colors I use, etc.

Nice to have

Should not have

```html
<!DOCTYPE html>
<html lang="en">
<head>
<meta charset="utf-8">
<title>LVP Business Card</title>
<link rel="stylesheet" href="https://fonts.googleapis.com/css2?family=Noto+Sans:ital,wght@0,400;0,700;1,400&display=swap">
<style>
  :root {
    --stage: #3a3532;
    --brand-blue: #0e76bd;
    --paper: #ffffff;
    --ink: #4a4a4a;
    --ink-soft: #666666;
    --rule: #5a5a5a;
  }
  * { box-sizing: border-box; margin: 0; padding: 0; }
  html, body {
    width: 1200px; height: 716px; overflow: hidden;
    background: var(--stage);
    font-family: "Noto Sans", sans-serif;
  }
  .stage {
    width: 1200px; height: 716px;
    display: flex; align-items: center; justify-content: center; gap: 40px;
  }
  .card {
    width: 540px; height: 309px;
    position: relative;
    box-shadow: 0 12px 30px rgba(0,0,0,0.45);
  }
  .card--front { background: var(--brand-blue); color: var(--paper); }
  .card--back { background: var(--paper); }

  .brand {
    position: absolute; top: 92px; left: 0; right: 0;
    display: flex; align-items: center; justify-content: center; gap: 12px;
  }
  .brand__dot {
    width: 14px; height: 14px; border-radius: 50%; background: var(--paper);
  }
  .brand__name {
    font-weight: 700; font-size: 64px; letter-spacing: 2px; line-height: 1;
    color: var(--paper);
  }
  .tagline {
    position: absolute; left: 0; right: 0; bottom: 40px;
    text-align: center; font-size: 13px; font-style: italic; letter-spacing: 0.2px;
  }

  .identity {
    position: absolute; top: 126px; right: 290px; text-align: right;
  }
  .identity__name {
    color: var(--brand-blue); font-weight: 700; font-size: 17px;
    text-transform: uppercase; letter-spacing: 0.5px; line-height: 1.2;
  }
  .identity__role { color: var(--ink-soft); font-size: 13px; line-height: 1.4; }
  .divider {
    position: absolute; top: 120px; left: 262px; width: 1px; height: 68px;
    background: var(--rule);
  }
  .contact {
    position: absolute; top: 124px; left: 278px; list-style: none;
    font-size: 12.5px; color: var(--ink); line-height: 20px;
  }
  .contact li { display: flex; align-items: center; gap: 6px; white-space: nowrap; }
  .contact svg { width: 10px; height: 10px; flex: none; fill: var(--brand-blue); }
  .contact .accent { color: var(--brand-blue); }
</style>
</head>
<body>
  <main class="stage">
    <section class="card card--front" aria-label="Card front">
      <div class="brand">
        <span class="brand__name">LVP</span>
        <span class="brand__dot" aria-hidden="true"></span>
      </div>
      <p class="tagline">Boost Sales Using Rewards &bull; Incentives &amp; Giveaways &bull; Get A Free Sample Package</p>
    </section>

    <section class="card card--back" aria-label="Card back">
      <div class="identity">
        <p class="identity__name">Doug Fenwick</p>
        <p class="identity__role">President, CEO</p>
      </div>
      <div class="divider" aria-hidden="true"></div>
      <ul class="contact">
        <li>
          <svg viewBox="0 0 10 10" aria-hidden="true"><path d="M2 0.5l1.6 2.2-1 1c.6 1.3 1.4 2.1 2.7 2.7l1-1L8.5 7 8 9C4.5 9 1 5.5 1 1z"/></svg>
          1-555-302-4196
        </li>
        <li>
          <svg viewBox="0 0 10 10" aria-hidden="true"><path d="M0 2h10v6H0z M0.6 2.4L5 5.6 9.4 2.4" stroke="#fff" stroke-width="0.8"/></svg>
          doug@boldpromoperksgroup.example
        </li>
        <li>
          <svg viewBox="0 0 10 10" aria-hidden="true"><circle cx="5" cy="5" r="4.6"/><path d="M0.6 5h8.8M5 0.4v9.2" stroke="#fff" stroke-width="0.7"/></svg>
          <span>www.<span class="accent">BoldPromoPerksGroup</span>.example</span>
        </li>
      </ul>
    </section>
  </main>
</body>
</html>
```